Brightfen Business Card Redesign & Logo Update

We need to update our business cards to something more modern and fresh. Brightfen can provide the current color schemes and old design examples, but welcome creativity in helping us with this redesign. PLEASE NOTE that we no longer utilize the "tree" and/or "leaf" imagery in our branding. If able would apprecaite an update on the quality of our "words only" logo in Ai. / PNG formats too.

Target Market(s)

Investors, landowners, corporate partners, contractors

Industry/Entity Type

Environmental Restoration & Conservation

Contact Information for Business Card

Logo, persons name, title, mailing address, phone and email, website url

Font styles to use
Other font styles liked:
• Merriweather

Requirements
Nice to have
• Logo, persons name, title, mailing address, phone and email, website url, but open to ideams
Should not have
• No all back backgrounds

```html
<!DOCTYPE html>
<html lang="en">
<head>
<meta charset="utf-8">
<title>Brightfen Business Card</title>
<link href="https://fonts.googleapis.com/css2?family=Oswald:wght@500&family=Fira+Sans:wght@400;600&display=swap" rel="stylesheet">
<style>
  :root {
    --backdrop: #e6e6e6;
    --forest: #137640;
    --ember: #e87722;
    --paper: #f4f4f4;
    --ink: #1b1b1b;
    --white: #ffffff;
  }
  * { margin: 0; padding: 0; box-sizing: border-box; }
  html, body { width: 1200px; height: 960px; overflow: hidden; }
  body { position: relative; background: var(--backdrop); font-family: "Fira Sans", sans-serif; }

  .card { position: absolute; left: 295px; width: 609px; height: 348px; overflow: hidden; }
  .card-front { top: 109px; background: var(--forest); }
  .card-back { top: 511px; background: var(--forest); }

  .brand { position: absolute; left: 0; width: 100%; text-align: center; font-family: "Oswald", sans-serif; font-weight: 500; }
  .brand-name { display: block; letter-spacing: 2px; line-height: 1; white-space: nowrap; }
  .brand-tagline { display: block; letter-spacing: 0.2px; line-height: 1; white-space: nowrap; }

  .card-front .brand { top: 160px; }
  .card-front .brand-name { font-size: 56px; color: var(--white); }
  .card-front .brand-tagline { margin-top: 30px; font-size: 18.5px; color: var(--white); }

  .back-panel { position: absolute; left: 0; top: 0; width: 304px; height: 100%; background: var(--paper); }
  .card-back .brand { top: 170px; padding-left: 8px; }
  .card-back .brand-name { font-size: 48px; color: var(--forest); }
  .card-back .brand-tagline { margin-top: 28px; font-size: 16.2px; color: var(--ink); }

  .contact { position: absolute; left: 349px; top: 91px; color: var(--white); font-size: 15.5px; line-height: 20.5px; }
  .contact-name { color: var(--ember); font-weight: 600; font-size: 19px; line-height: 24px; }
  .contact-title { margin-bottom: 18px; }
  .contact-row { display: flex; align-items: flex-start; gap: 6px; }
  .contact-row.spaced { margin-bottom: 4px; }
  .contact-icon { width: 13px; height: 13px; margin-top: 4px; flex: none; }
  .contact-icon * { fill: none; stroke: var(--ember); stroke-width: 1.6; }
</style>
</head>
<body>
  <section class="card card-front">
    <div class="brand">
      <span class="brand-name">BRIGHTFEN</span>
      <span class="brand-tagline">ENVIRONMENTAL CREDIT COMPANY</span>
    </div>
  </section>

  <section class="card card-back">
    <div class="back-panel">
      <div class="brand">
        <span class="brand-name">BRIGHTFEN</span>
        <span class="brand-tagline">ENVIRONMENTAL CREDIT COMPANY</span>
      </div>
    </div>
    <div class="contact">
      <div class="contact-name">Daniel Harper</div>
      <div class="contact-title">Owner</div>
      <div class="contact-row spaced">
        <svg class="contact-icon" viewBox="0 0 14 14"><path d="M7 13s-4.5-4.6-4.5-7.5a4.5 4.5 0 0 1 9 0C11.5 8.4 7 13 7 13z"/><circle cx="7" cy="5.5" r="1.6"/></svg>
        <span>418 Meadow Lane, Suite 210<br>Fairmont, CA 95104</span>
      </div>
      <div class="contact-row">
        <svg class="contact-icon" viewBox="0 0 14 14"><path d="M3 1.5l2.2 2.6-1.3 1.6a8 8 0 0 0 4.4 4.4l1.6-1.3 2.6 2.2-1.4 1.5C6.3 12.5 1.5 7.7 1.5 2.9z"/></svg>
        <span>555-204-7781</span>
      </div>
      <div class="contact-row">
        <svg class="contact-icon" viewBox="0 0 14 14"><rect x="1" y="2.5" width="12" height="9"/><path d="M1 3l6 5 6-5"/></svg>
        <span>daniel@brightfen.com</span>
      </div>
      <div class="contact-row">
        <svg class="contact-icon" viewBox="0 0 14 14"><circle cx="7" cy="7" r="6"/><ellipse cx="7" cy="7" rx="2.6" ry="6"/><path d="M1 7h12"/></svg>
        <span>www.brightfen.com</span>
      </div>
    </div>
  </section>
</body>
</html>
```